Flat Belly Design Graphics for Social

I want to create 9 social media graphics (new Instagram size 4:5 (1080 x 1350 pixels) focusing on our Flat Belly Graphics, using the pics attached. Use the attached pics, NO RANDOM STOCK PHOTOGRAPHY. For the color scheme of the graphics, the color palette is attached. YOU MUST POST ALL 9 GRAPHICS IN ONE ENTRY.
Using the 3 titles below, create one set of graphics. 1) with all text, then for the others, use the pictures as detailed below in IMPORTANT:
1. Ten-Week Bright Morning Reboot
2. The Quick Garden Kitchen Menu Guide
3. Studio Habits for Lasting Energy Past Midlife - Zero Gym Needed
IMPORTANT:
Only use RK Pic 1 and RK Pic 2 with the title, Ten-Week Bright Morning Reboot
Only use meal plan1 and meal plan2 pics with the title, Quick Garden Kitchen Menu Guide
Only use studio habits 1 and studio habits 2 pics with the title, Studio Habits for Lasting Energy Past Midlife - Zero Gym Needed
women over 40

```html
<!DOCTYPE html>
<html lang="en">
<head>
<meta charset="utf-8">
<title>Social Graphics Set</title>
<link rel="stylesheet" href="https://fonts.googleapis.com/css2?family=Oswald:wght@400;500;600;700&family=Anton&display=swap">
<style>
:root{
  --bg:#120207;
  --green:#2f4c4a;
  --deep:#254543;
  --pink:#e298b0;
  --rose:#df7f9c;
  --blush:#fbeeef;
  --petal:#f8d6e2;
  --teal:#3f9c8f;
  --white:#ffffff;
}
*{margin:0;padding:0;box-sizing:border-box}
html,body{width:1074px;height:1200px;overflow:hidden;background:var(--bg)}
body{position:relative;font-family:'Oswald',sans-serif}
.card{position:absolute;width:259px;height:324px;overflow:hidden}
.c1{left:122px;top:94px}.c2{left:408px;top:94px}.c3{left:693px;top:94px}
.r2{top:438px}.r3{top:782px}
.shape{position:absolute;inset:0;width:100%;height:100%}
.t{position:absolute;line-height:.95;white-space:nowrap}
.display{font-family:'Anton','Oswald',sans-serif;font-weight:400}
.bold{font-weight:700}
.spaced{letter-spacing:.22em}
.photo{position:absolute}
.shadow{text-shadow:2px 2px 2px rgba(0,0,0,.35)}
</style>
</head>
<body>

<!-- Row 1 : text only -->
<section class="card c1" style="background:var(--blush)">
  <svg class="shape" viewBox="0 0 259 324"><polygon points="259,0 259,324 0,324" fill="var(--pink)"/></svg>
  <div class="t bold" style="left:21px;top:34px;font-size:34px;color:var(--rose)">TEN-WEEK</div>
  <div class="t display" style="left:20px;top:76px;font-size:66px;color:var(--green)">BRIGHT</div>
  <div class="t display" style="left:20px;top:150px;font-size:52px;color:var(--green)">MORNING</div>
  <div class="t bold" style="left:145px;top:260px;font-size:32px;color:var(--white);background:var(--green);padding:4px 6px">Reboot</div>
</section>

<section class="card c2" style="background:var(--green)">
  <div class="t bold" style="left:35px;top:22px;font-size:32px;color:var(--white)">The Quick</div>
  <div class="t display" style="left:33px;top:62px;font-size:72px;color:var(--rose)">Garden</div>
  <div class="t display" style="left:33px;top:150px;font-size:62px;color:var(--rose)">KITCHEN</div>
  <div class="t bold" style="left:35px;top:240px;font-size:42px;color:var(--white)">Menu Guide</div>
</section>

<section class="card c3" style="background:var(--blush)">
  <svg class="shape" viewBox="0 0 259 324"><polygon points="0,0 259,324 0,324" fill="var(--pink)"/></svg>
  <div class="t bold" style="right:16px;top:18px;font-size:18px;color:var(--rose)">Studio Habits for</div>
  <div class="t display" style="right:16px;top:44px;font-size:64px;color:var(--green)">LASTING</div>
  <div class="t display" style="right:16px;top:122px;font-size:64px;color:var(--green)">ENERGY</div>
  <div class="t display" style="right:16px;top:200px;font-size:44px;color:var(--green)">PAST MIDLIFE</div>
  <div class="t bold" style="left:16px;top:272px;font-size:24px;color:var(--white)">Zero Gym Needed</div>
</section>

<!-- Row 2 -->
<section class="card c1 r2" style="background:var(--green)">
  <div style="position:absolute;left:0;top:90px;width:259px;height:124px;background:var(--blush)"></div>
  <div class="t bold" style="left:0;width:259px;text-align:center;top:16px;font-size:34px;color:var(--white)">Ten - Week</div>
  <div class="photo" role="img" aria-label="Portrait photo: smiling woman in a white crop top pointing at her waist" style="left:44px;top:66px;width:172px;height:172px;border-radius:50%;background:radial-gradient(circle at 50% 45%,#ece4e2 0 30%,var(--pink) 75%);border:4px solid var(--blush)"></div>
  <div class="t bold" style="left:0;width:259px;text-align:center;top:246px;font-size:32px;color:var(--white)">BRIGHT MORNING</div>
  <div class="t bold spaced" style="left:0;width:259px;text-align:center;top:290px;font-size:19px;color:var(--white)">Reboot</div>
</section>

<section class="card c2 r2" style="background:var(--blush)">
  <svg class="shape" viewBox="0 0 259 324"><polygon points="259,128 259,324 0,324 0,319" fill="var(--pink)"/></svg>
  <div class="t bold" style="left:0;width:259px;text-align:center;top:34px;font-size:21px;color:var(--teal)">The Quick</div>
  <div class="t display" style="left:0;width:259px;text-align:center;top:60px;font-size:36px;color:var(--green)">GARDEN KITCHEN</div>
  <div class="t bold spaced" style="left:32px;width:195px;text-align:center;top:105px;font-size:19px;line-height:23px;color:var(--green);background:var(--petal)">Menu Guide</div>
  <div class="photo" role="img" aria-label="Food photo: chicken, fruit, asparagus and a meal plan sheet on a wooden table" style="left:27px;top:148px;width:206px;height:148px;background:linear-gradient(135deg,#e7b6a4,#6b4a36 45%,#c7463f 70%,#8a9b4a)"></div>
</section>

<section class="card c3 r2" style="background:var(--blush)">
  <div style="position:absolute;left:0;top:191px;width:259px;height:5px;background:var(--green)"></div>
  <div style="position:absolute;left:0;top:198px;width:259px;height:126px;background:var(--green)"></div>
  <div class="t bold" style="left:0;width:259px;text-align:center;top:22px;font-size:22px;color:var(--teal)">Studio Habits for</div>
  <div class="t display" style="left:0;width:259px;text-align:center;top:48px;font-size:38px;color:var(--green)">LASTING ENERGY</div>
  <div class="photo" role="img" aria-label="Photo: two women sharing a whispered secret" style="left:20px;top:106px;width:225px;height:144px;border-radius:36px;background:linear-gradient(120deg,#3b2a24,#b98266 45%,#f2e6e2 70%,#6e4a3c)"></div>
  <div class="t bold" style="left:27px;width:205px;text-align:center;top:264px;font-size:16px;line-height:24px;color:var(--white);background:var(--pink)">Past Midlife - Zero Gym Needed</div>
</section>

<!-- Row 3 -->
<section class="card c1 r3" style="background:var(--pink)">
  <div class="photo" role="img" aria-label="Photo: smiling woman in a white crop top standing in a kitchen" style="left:0;top:0;width:130px;height:324px;background:linear-gradient(180deg,#5a3d31,#b08c78 40%,#f1ece9 60%,#1c1a1b 80%)"></div>
  <div class="t bold shadow" style="left:142px;top:42px;font-size:20px;color:var(--white)">Ten - Week</div>
  <div class="t display shadow" style="left:142px;top:70px;font-size:40px;color:var(--white)">BRIGHT</div>
  <div class="t bold shadow" style="left:142px;top:122px;font-size:29px;color:var(--white)">Morning</div>
  <div class="t display shadow" style="left:142px;top:220px;font-size:38px;color:var(--white)">REBOOT</div>
</section>

<section class="card c2 r3" style="background:var(--blush)">
  <div style="position:absolute;left:0;top:0;width:259px;height:55px;background:var(--green)"></div>
  <div style="position:absolute;left:0;top:255px;width:259px;height:3px;background:var(--green)"></div>
  <div style="position:absolute;left:0;top:261px;width:259px;height:63px;background:var(--green)"></div>
  <div class="t bold shadow" style="left:0;width:259px;text-align:center;top:8px;font-size:36px;color:var(--rose)">The Quick</div>
  <div class="t display" style="left:0;width:259px;text-align:center;top:70px;font-size:36px;color:#1f5f58">GARDEN KITCHEN</div>
  <div class="t bold spaced" style="left:21px;width:217px;text-align:center;top:120px;font-size:20px;line-height:26px;color:var(--white);background:var(--pink)">Menu Guide</div>
  <div class="photo" role="img" aria-label="Food photo: vegetables, fruit and salmon around a notepad meal plan" style="left:19px;top:160px;width:222px;height:142px;border:3px solid var(--white);border-radius:0 0 8px 8px;background:linear-gradient(135deg,#d9402f,#e9a43b 30%,#4b3a30 55%,#3f7a35 80%,#c9392c)"></div>
</section>

<section class="card c3 r3" style="background:var(--blush)">
  <div style="position:absolute;left:0;top:0;width:167px;height:190px;background:var(--pink);border-radius:0 0 60px 0"></div>
  <div style="position:absolute;left:5px;top:130px;width:4px;height:194px;background:var(--green)"></div>
  <div style="position:absolute;left:12px;top:130px;width:4px;height:194px;background:var(--green)"></div>
  <div style="position:absolute;left:197px;top:0;width:62px;height:324px;background:var(--green)"></div>
  <div class="photo" role="img" aria-label="Photo: two women, one whispering to the other" style="left:8px;top:10px;width:160px;height:182px;border-radius:0 0 60px 0;background:linear-gradient(120deg,#d3a184,#f0ddd4 40%,#3a2a24 60%,#8ab0d0)"></div>
  <div class="t bold" style="left:27px;top:212px;font-size:17px;color:var(--bg)">Studio Habits for</div>
  <div class="t display" style="left:27px;top:234px;font-size:25px;color:var(--green)">LASTING ENERGY</div>
  <div class="t" style="left:30px;top:268px;font-size:23px;font-weight:400;color:var(--bg)">Past Midlife</div>
  <div class="t display" style="left:228px;top:162px;font-size:29px;color:var(--white);transform:translate(-50%,-50%) rotate(-90deg)">ZERO GYM NEEDED</div>
</section>

</body>
</html>
```